Velk Partners Building Business Cards

We need a business card that reflects our business as "Solar Experts" in San Diego. Browse our website www.velkpartners.example our License needs to be displayed as "CSLB# 3867140" our phone number is (619) 555-0187

Save thousands on your electric bills and increase the value of your home while helping to protect the environment. Our solar installation experts will help you design the system that's right for you, using only the highest quality equipment that will look great and give you ideal performance. Our goal is to make you energy independent, and get your electric bill to 0.

Paul Osterby
(619) 555-0187
paul@velkpartners.example

Target Market(s)

Home owners in san diego looking for solar

Industry/Entity Type

Solar Energy

Contact Information for Business Card

Paul Osterby
(619) 555-0187
paul@velkpartners.example

Font styles to use
Other font styles liked:
• Use our logo font

Requirements
Must have
• License needs to be displayed as "CSLB# 3867140" our phone number is (619) 555-0187
Nice to have
• Real images of rooftop home solar in san diego
Should not have
• our business address

```html
<!DOCTYPE html>
<html lang="en">
<head>
<meta charset="utf-8">
<title>Velk Partners Building – Business Cards</title>
<link href="https://fonts.googleapis.com/css2?family=Open+Sans:wght@400;600;700&display=swap" rel="stylesheet">
<style>
  :root {
    --navy: #193a73;
    --sun: #f7a900;
    --paper: #ffffff;
    --stage: #eceff0;
    --ink-light: #ffffff;
  }
  * { margin: 0; padding: 0; box-sizing: border-box; }
  html, body { width: 1200px; height: 812px; overflow: hidden; background: var(--stage); }
  body { font-family: "Open Sans", Arial, sans-serif; position: relative; }

  .card {
    position: absolute;
    top: 258px;
    width: 520px;
    height: 297px;
    overflow: hidden;
    box-shadow: 0 6px 18px rgba(0,0,0,0.12);
  }

  /* Back side */
  .card--back { left: 50px; background: var(--navy); }
  .brand-lockup {
    position: absolute;
    left: 0; right: 0; top: 100px;
    display: flex; align-items: center; justify-content: center; gap: 14px;
  }
  .brand-dot { width: 34px; height: 34px; border-radius: 50%; background: var(--sun); }
  .brand-name { color: var(--ink-light); font-weight: 700; font-size: 28px; letter-spacing: 0.5px; }
  .back-url {
    position: absolute; left: 0; right: 0; top: 210px;
    text-align: center; color: var(--ink-light);
    font-size: 13px; letter-spacing: 2.6px;
  }

  /* Front side */
  .card--front { left: 630px; background: var(--paper); }
  .front-shapes { position: absolute; inset: 0; }
  .front-logo {
    position: absolute; left: 28px; bottom: 44px;
    color: var(--navy); font-weight: 700; font-size: 25px; letter-spacing: -0.3px;
  }
  .contact {
    position: absolute; right: 30px; top: 32px;
    text-align: right; color: var(--ink-light);
    font-size: 12.5px; line-height: 1.55;
  }
  .contact__name { color: var(--sun); font-weight: 700; font-size: 19px; line-height: 1.2; }
  .contact__title { font-size: 13px; margin-bottom: 6px; }
  .contact__line { display: flex; align-items: center; justify-content: flex-end; gap: 6px; }
  .contact__icon { width: 12px; height: 12px; flex: none; }
</style>
</head>
<body>

<section class="card card--back" aria-label="Card back">
  <div class="brand-lockup">
    <span class="brand-dot"></span>
    <span class="brand-name">Velk Partners Building</span>
  </div>
  <p class="back-url">WWW.VELKPARTNERS.EXAMPLE</p>
</section>

<section class="card card--front" aria-label="Card front">
  <svg class="front-shapes" width="520" height="297" viewBox="0 0 520 297">
    <polygon points="205,0 520,0 520,285 280,212" fill="var(--sun)"/>
    <polygon points="214,0 520,0 520,272 288,202" fill="var(--navy)"/>
  </svg>

  <p class="front-logo">Velk Partners Building</p>

  <div class="contact">
    <p class="contact__name">Paul Osterby</p>
    <p class="contact__title">CEO/Founder</p>
    <p class="contact__line">CSLB# 3867140</p>
    <p class="contact__line">(619) 555-0187
      <svg class="contact__icon" viewBox="0 0 12 12"><path d="M2.5 1 L4.5 1 L5.3 3.5 L4 4.5 Q5 7 7.5 8 L8.5 6.7 L11 7.5 L11 9.5 Q10.5 11 9 11 Q1 10 1 2.5 Q1 1 2.5 1Z" fill="var(--sun)"/></svg>
    </p>
    <p class="contact__line">paul@velkpartners.example
      <svg class="contact__icon" viewBox="0 0 12 12"><rect x="1" y="2.5" width="10" height="7" fill="var(--sun)"/><path d="M1 2.5 L6 6.5 L11 2.5" stroke="var(--navy)" stroke-width="1" fill="none"/></svg>
    </p>
    <p class="contact__line">www.velkpartners.example
      <svg class="contact__icon" viewBox="0 0 12 12"><circle cx="6" cy="6" r="5.2" fill="var(--sun)"/><path d="M1 6 H11 M6 1 Q3 6 6 11 M6 1 Q9 6 6 11" stroke="var(--navy)" stroke-width="0.8" fill="none"/></svg>
    </p>
  </div>
</section>

</body>
</html>
```